BildeVOLD buisnesscard

Hey :) I need a modern buisnesscard for my company BildeVOLD
It most have:
Dagligleder og Fotograf: Henrik Audun Strandvik

Mob: +4791264085
Epost: post@bildevold.example
Adresse: Kvernbakken9, 6040 Langevåg

Facbook and instagram logo with text BildeVOLD

BildeVOLD logo

It Company

```html
<!DOCTYPE html>
<html lang="no">
<head>
<meta charset="utf-8">
<title>BildeVOLD – visittkort</title>
<link href="https://fonts.googleapis.com/css2?family=Lato:wght@400;700&display=swap" rel="stylesheet">
<style>
  :root {
    --stage: #3a3a3a;
    --card: #050505;
    --ink: #ffffff;
    --silver: #bdbcbd;
    --muted: #a8a8a8;
    --rule: #8a8a8a;
  }
  * { box-sizing: border-box; margin: 0; padding: 0; }
  html, body {
    width: 1200px; height: 900px; overflow: hidden;
    background: var(--stage);
    font-family: "Lato", Arial, sans-serif;
  }
  .card {
    position: absolute; left: 270px;
    width: 660px; height: 377px;
    background: var(--card);
    overflow: hidden;
    box-shadow: 0 10px 30px rgba(0,0,0,.45);
  }
  .card--front { top: 48px; }
  .card--back { top: 475px; }

  .brand {
    display: flex; align-items: center; gap: 14px;
    color: var(--silver); font-weight: 700; letter-spacing: .5px;
  }
  .brand__mark { background: var(--silver); }
  .card--front .brand {
    position: absolute; left: 0; right: 0; top: 150px;
    justify-content: center; font-size: 54px;
  }
  .card--front .brand__mark { width: 40px; height: 40px; }

  .card--back .brand {
    position: absolute; left: 34px; top: 38px; font-size: 38px;
  }
  .card--back .brand__mark { width: 30px; height: 30px; }

  .divider {
    position: absolute; left: 34px; right: 34px; top: 108px;
    height: 1px; background: var(--rule);
  }
  .social {
    position: absolute; left: 34px; top: 124px;
    list-style: none; color: var(--ink); font-size: 15px; line-height: 21px;
  }
  .social li { display: flex; align-items: center; gap: 9px; }
  .social svg { width: 13px; height: 13px; flex: none; }

  .person {
    position: absolute; right: 40px; top: 168px; text-align: right;
  }
  .person__name {
    color: var(--ink); font-size: 26px; font-weight: 400;
    padding-bottom: 6px; border-bottom: 1px solid var(--rule);
  }
  .person__role { color: var(--muted); font-size: 18px; margin-top: 4px; }
  .address {
    position: absolute; right: 40px; top: 262px; text-align: right;
    color: var(--ink); font-size: 19px; line-height: 24px; font-style: normal;
  }
  .swoosh { position: absolute; left: 0; bottom: 0; width: 660px; height: 140px; }
  .email {
    position: absolute; right: 40px; bottom: 8px;
    color: var(--ink); font-size: 19px;
  }
</style>
</head>
<body>
  <section class="card card--front" aria-label="Visittkort forside">
    <div class="brand"><span class="brand__mark"></span>BildeVOLD</div>
  </section>

  <section class="card card--back" aria-label="Visittkort bakside">
    <div class="brand"><span class="brand__mark"></span>BildeVOLD</div>
    <div class="divider"></div>

    <ul class="social">
      <li>
        <svg viewBox="0 0 13 13" aria-hidden="true"><rect x="3" y="0.5" width="7" height="12" rx="1.2" fill="none" stroke="#bdbcbd"/><rect x="5" y="10" width="3" height="1" fill="#bdbcbd"/></svg>
        +4791264085
      </li>
      <li>
        <svg viewBox="0 0 13 13" aria-hidden="true"><rect width="13" height="13" rx="2" fill="#bdbcbd"/></svg>
        BildeVOLD
      </li>
      <li>
        <svg viewBox="0 0 13 13" aria-hidden="true"><circle cx="6.5" cy="6.5" r="6.5" fill="#bdbcbd"/></svg>
        BildeVOLD
      </li>
    </ul>

    <div class="person">
      <h1 class="person__name">Henrik Audun Strandvik</h1>
      <p class="person__role">Dagligleder og Fotograf</p>
    </div>
    <address class="address">Kvernbakken 9<br>6040 Fjellvika</address>

    <svg class="swoosh" viewBox="0 0 660 140" preserveAspectRatio="none" aria-hidden="true">
      <path d="M0 28 C140 50 300 95 560 110 C300 105 120 70 0 52 Z" fill="#ffffff"/>
      <path d="M0 60 C120 80 280 110 420 108 L660 108 L660 140 L0 140 Z" fill="#bdbcbd"/>
    </svg>
    <p class="email">post@bildevold.example</p>
  </section>
</body>
</html>
```